Economics of an Assumption vs Obtaining a New Loan at Current Market Rate

I need to marketing flyer that has fields that calculate mortgage payments amongst other calculations. I have a rough draft that I will attach.

The idea is to provide a tool for a real estate agent to use to illustrate to a potential buyer what a payment would be if they assumed the existing loan on the house or took out a new loan at current market.

The flyer needs to be able to allow an agent to drop in their logo, photo, and contact along with the loan officers photo and contact info.

You can google open house flyer to see examples of what the overall artwork and presentation can look like.

Target Market(s)

Home Buyers

Industry/Entity Type

Real Estate

Colors
F0912C
F2A743
F7CA91
FBE8D2
FDF5EE
EE7325
F08F49
F5BC92
FAE3D3
FDF4ED

Requirements
Must have
• A way to calculate mortgage payment
Nice to have
• Photo and logo drop ins

```html
<!DOCTYPE html>
<html lang="en">
<head>
<meta charset="utf-8">
<title>Assumption vs New Loan – Flyer</title>
<link href="https://fonts.googleapis.com/css2?family=Poppins:wght@400;500;600;700;800&display=swap" rel="stylesheet">
<style>
:root{
  --orange:#EE7325;
  --orange-2:#F0912C;
  --orange-soft:#F5BC92;
  --cream:#FDF5EE;
  --dark:#3b3b3b;
  --ink:#222222;
  --line:#9a9a9a;
  --bg:#f4f4f4;
  --white:#ffffff;
}
*{box-sizing:border-box;margin:0;padding:0}
html,body{width:1200px;height:2928px;overflow:hidden;background:var(--bg);font-family:'Poppins',sans-serif;color:var(--ink)}
.flyer{position:absolute;left:100px;top:769px;width:1000px;height:1390px;background:var(--white);box-shadow:0 10px 40px rgba(0,0,0,.12);overflow:hidden}
.abs{position:absolute}
.corner-block{left:730px;top:60px;width:270px;height:180px;background:var(--orange)}
.hero-photo{left:506px;top:72px;width:440px;height:260px;background:linear-gradient(180deg,#a9c4e3 0%,#d9e3ee 45%,#b58a66 60%,#8d6a4c 100%);border:4px solid var(--white)}
.brand{left:51px;top:70px;display:flex;align-items:center;gap:14px}
.brand-dot{width:46px;height:46px;border-radius:50%;background:var(--orange)}
.brand-name{font-size:50px;font-weight:600;color:var(--orange);letter-spacing:.5px}
.price-box{left:51px;top:190px;width:434px;height:172px;border:4px solid var(--orange);border-radius:10px;overflow:hidden}
.price-box h2{background:var(--orange);color:var(--white);font-size:34px;font-weight:700;padding:14px 20px;height:72px}
.price-field{margin:16px 22px;height:62px;border:3px solid var(--orange);border-radius:8px;background:var(--white)}
.mortgage{top:400px;width:440px}
.mortgage.current{left:51px}
.mortgage.new{left:520px}
.m-head{display:flex;align-items:center;height:48px;margin-bottom:14px}
.m-head .word{font-size:26px;font-weight:800;padding:4px 14px;border:3px solid var(--dark);height:46px;line-height:36px}
.m-head .word.fill{background:var(--orange);border-color:var(--orange);color:var(--white)}
.m-head .down{margin-left:12px;display:flex;align-items:center;gap:6px}
.m-head .down b{font-size:34px;font-weight:800}
.m-head .down small{font-size:10px;font-weight:700;line-height:1.1;text-transform:uppercase}
.row{display:flex;align-items:center;justify-content:space-between;height:32px;margin-bottom:4px;font-size:17px;font-weight:500}
.field{flex:none;width:210px;height:26px;border:2px solid var(--line);border-radius:4px;font-size:11px;line-height:22px;padding-left:8px;color:#555;white-space:nowrap;overflow:hidden;font-weight:400}
.field.long{font-size:8.5px;padding-left:5px;letter-spacing:-.1px;color:var(--ink);font-weight:500}
.row.total{background:var(--orange);color:var(--white);font-weight:700;padding-left:10px;border-radius:3px}
.row.total .field{border-color:var(--white);background:var(--white)}
.term{display:flex;align-items:center;gap:8px;font-size:15px;font-weight:600;margin-top:14px}
.term .mini{width:76px;height:24px;border:2px solid var(--line);border-radius:4px;font-size:9px;line-height:20px;padding-left:5px;color:#777;font-weight:400}
.term .note{font-weight:400}
.delta{display:flex;align-items:center;margin-top:22px;height:38px;border:2px solid var(--orange);border-radius:4px;overflow:hidden}
.delta .tag{background:var(--orange);color:var(--white);font-weight:700;font-size:13px;padding:0 12px;height:100%;line-height:36px}
.delta .text{font-size:12px;font-weight:600;padding-left:12px;text-transform:uppercase;white-space:nowrap}
.result{top:750px;height:102px;border-radius:12px;color:var(--white);font-size:36px;font-weight:800;line-height:1.1;display:flex;align-items:center;justify-content:center;text-align:center;text-transform:uppercase}
.result.payment{left:72px;width:380px;background:var(--dark)}
.result.totals{left:468px;width:490px;background:var(--orange)}
.certified{top:882px;left:0;width:1000px;text-align:center;font-size:38px;font-weight:700;color:var(--dark);white-space:nowrap}
.agent-photo{left:51px;top:955px;width:285px;height:345px;border-radius:12px;border:4px solid var(--orange);background:linear-gradient(160deg,#cfd4da 0%,#eef0f2 50%,#b8a48f 100%)}
.contact-card{top:955px;width:190px;height:345px;border:3px solid var(--dark);border-radius:12px;overflow:hidden}
.contact-card.one{left:352px}
.contact-card.two{left:558px}
.contact-card h3{background:var(--dark);color:var(--white);font-size:13px;font-weight:700;text-align:center;padding:10px 6px;line-height:1.2;text-transform:uppercase}
.c-item{display:flex;flex-direction:column;align-items:center;margin-top:16px;font-size:13px;font-weight:600;white-space:nowrap}
.c-item svg{width:38px;height:38px;margin-bottom:6px}
.logo-card{left:764px;top:955px;width:196px;height:345px;border:3px solid var(--dark);border-radius:12px;display:flex;align-items:center;justify-content:center;gap:8px}
.logo-card .brand-dot{width:26px;height:26px}
.logo-card .brand-name{font-size:30px}
.website{left:0;top:1334px;width:1000px;text-align:center;font-size:24px;font-weight:700;letter-spacing:6px;color:var(--dark)}
</style>
</head>
<body>
<main class="flyer">
  <div class="abs corner-block"></div>
  <div class="abs hero-photo" role="img" aria-label="Photo of the listed house"></div>

  <div class="abs brand"><span class="brand-dot"></span><span class="brand-name">Nestwise</span></div>

  <section class="abs price-box">
    <h2>PURCHASE PRICE</h2>
    <div class="price-field"></div>
  </section>

  <section class="abs mortgage current">
    <div class="m-head"><span class="word">CURRENT</span><span class="word fill">MORTGAGE</span></div>
    <div class="row"><span>Loan amount</span><span class="field">Allow Input</span></div>
    <div class="row"><span>Interest rate</span><span class="field">Allow Input</span></div>
    <div class="row"><span>Principle Interest</span><span class="field">Allow Input</span></div>
    <div class="row"><span>Mortgage Insurance</span><span class="field">Allow Input</span></div>
    <div class="row total"><span>TOTAL</span><span class="field"></span></div>
    <div class="term"><span>Years</span><span class="mini">input</span><span>Months</span><span class="mini">input</span><span class="note">left on loan</span></div>
    <div class="delta"><span class="tag">DELTA</span><span class="text">Purchase price minus loan amount</span></div>
  </section>

  <section class="abs mortgage new">
    <div class="m-head"><span class="word">NEW</span><span class="word fill">MORTGAGE</span><span class="down"><b>10%</b><small>Down<br>Payment</small></span></div>
    <div class="row"><span>Loan amount</span><span class="field">10% of purchase price</span></div>
    <div class="row"><span>Interest rate</span><span class="field">Input</span></div>
    <div class="row"><span>Principle Interest</span><span class="field">Calc payment</span></div>
    <div class="row"><span>Mortgage Insurance</span><span class="field">Input %</span></div>
    <div class="row total"><span>TOTAL</span><span class="field long">Principal Interest + Mortgage Insurance</span></div>
    <div class="term"><span>Years</span><span class="mini">input</span><span>Months</span><span class="mini">input</span><span class="note">left on loan</span></div>
    <div class="delta"><span class="text">Down payment amount</span></div>
  </section>

  <div class="abs result payment">Payment<br>Difference</div>
  <div class="abs result totals">Difference<br>Between Totals</div>

  <p class="abs certified">THIS PROPERTY IS "TAKE MY LOW RATE CERTIFIED"</p>

  <div class="abs agent-photo" role="img" aria-label="Agent photo: house keys and small house model"></div>

  <section class="abs contact-card one">
    <h3>Contact<br>Information</h3>
    <div class="c-item"><svg viewBox="0 0 38 38"><circle cx="19" cy="19" r="19" fill="#3b3b3b"/><path d="M13 11l4 0 2 5-2.5 1.5a10 10 0 0 0 5 5L23 20l5 2v4a2 2 0 0 1-2 2A16 16 0 0 1 11 13a2 2 0 0 1 2-2z" fill="#EE7325"/></svg>555.010.2468</div>
    <div class="c-item"><svg viewBox="0 0 38 38"><circle cx="19" cy="19" r="19" fill="#3b3b3b"/><rect x="10" y="13" width="18" height="12" rx="1.5" fill="#EE7325"/><path d="M10 14l9 7 9-7" stroke="#3b3b3b" stroke-width="1.5" fill="none"/></svg>info@nestwise.com</div>
    <div class="c-item"><svg viewBox="0 0 38 38"><circle cx="19" cy="19" r="19" fill="#3b3b3b"/><circle cx="19" cy="19" r="9" fill="none" stroke="#EE7325" stroke-width="2"/><ellipse cx="19" cy="19" rx="4" ry="9" fill="none" stroke="#EE7325" stroke-width="2"/><path d="M10 19h18" stroke="#EE7325" stroke-width="2"/></svg>www.nestwise.com</div>
  </section>

  <section class="abs contact-card two">
    <h3>Contact<br>Information</h3>
    <div class="c-item"><svg viewBox="0 0 38 38"><circle cx="19" cy="19" r="19" fill="#3b3b3b"/><path d="M13 11l4 0 2 5-2.5 1.5a10 10 0 0 0 5 5L23 20l5 2v4a2 2 0 0 1-2 2A16 16 0 0 1 11 13a2 2 0 0 1 2-2z" fill="#EE7325"/></svg>555.010.2468</div>
    <div class="c-item"><svg viewBox="0 0 38 38"><circle cx="19" cy="19" r="19" fill="#3b3b3b"/><rect x="10" y="13" width="18" height="12" rx="1.5" fill="#EE7325"/><path d="M10 14l9 7 9-7" stroke="#3b3b3b" stroke-width="1.5" fill="none"/></svg>info@nestwise.com</div>
    <div class="c-item"><svg viewBox="0 0 38 38"><circle cx="19" cy="19" r="19" fill="#3b3b3b"/><circle cx="19" cy="19" r="9" fill="none" stroke="#EE7325" stroke-width="2"/><ellipse cx="19" cy="19" rx="4" ry="9" fill="none" stroke="#EE7325" stroke-width="2"/><path d="M10 19h18" stroke="#EE7325" stroke-width="2"/></svg>www.nestwise.com</div>
  </section>

  <div class="abs logo-card"><span class="brand-dot"></span><span class="brand-name">Nestwise</span></div>

  <p class="abs website">WWW.NESTWISE.com</p>
</main>
</body>
</html>
```